Halvor Grading and Septic needs a flyer to submit to contractors to offer our services

I need a sleek profession one page full color high gloss document showcasing our services to give to Mobile Home Companies and contractors that need our services.

Target Market(s)

Home Builders. Mobile Home Salesmen. People Building new homes.

Industry/Entity Type

Construction

Font styles to use
Serif
Sans Serif

Requirements
Must have
• Phone Number. Email address. Logo. Services offered: Mobile Home Pads, Meter Pole Placement and Connection, Waterline Connection, On Site Septic System Installs
Should not have
• Jokes, Nothing trying to be cute

```html
<!DOCTYPE html>
<html lang="en">
<head>
<meta charset="utf-8">
<title>Halvor Grading and Septic – Services Flyer</title>
<link href="https://fonts.googleapis.com/css2?family=Poppins:ital,wght@0,300;0,400;0,700;0,800;1,700&display=swap" rel="stylesheet">
<style>
  :root {
    --maroon: #4a0303;
    --blue: #175089;
    --title-blue: #1a4f86;
    --white: #ffffff;
    --body-text: #3a3a3a;
    --soil-light: #d4a26a;
    --soil-dark: #9c6a3a;
    --sky: #5f95d4;
    --grass: #7d8a4a;
  }
  * { box-sizing: border-box; margin: 0; padding: 0; }
  html, body { width: 848px; height: 1200px; overflow: hidden; background: var(--white); }
  .flyer {
    position: relative;
    width: 848px;
    height: 1200px;
    overflow: hidden;
    background: var(--white);
    font-family: "Poppins", sans-serif;
  }
  .backdrop { position: absolute; inset: 0; width: 848px; height: 1200px; }

  .brand {
    position: absolute;
    left: 42px;
    top: 56px;
    color: var(--blue);
    font-weight: 800;
    font-size: 30px;
    line-height: 1.12;
    text-transform: uppercase;
    letter-spacing: 0.5px;
  }

  .service {
    position: absolute;
    width: 199px;
    height: 413px;
    border-radius: 100px;
    background: var(--white);
    box-shadow: 0 6px 14px rgba(0, 0, 0, 0.28);
    text-align: center;
  }
  .service--pads   { left: 18px;  top: 690px; }
  .service--meter  { left: 223px; top: 615px; }
  .service--water  { left: 427px; top: 550px; }
  .service--septic { left: 631px; top: 462px; }

  .service__photo {
    position: absolute;
    left: 15px;
    top: 16px;
    width: 169px;
    height: 169px;
    border-radius: 50%;
  }
  .service--pads .service__photo   { background: linear-gradient(180deg, var(--sky) 0%, #dcdcd6 45%, var(--grass) 100%); }
  .service--meter .service__photo  { background: linear-gradient(180deg, #c9c3b4 0%, #bfb6a4 45%, #9a4a2c 100%); }
  .service--water .service__photo  { background: linear-gradient(180deg, #9fc2ea 0%, #c5c8c6 40%, #6b5848 100%); }
  .service--septic .service__photo { background: linear-gradient(180deg, var(--sky) 0%, #c9a54a 40%, var(--soil-light) 100%); }

  .service__title {
    position: absolute;
    left: 6px;
    right: 6px;
    top: 196px;
    color: var(--title-blue);
    font-weight: 700;
    font-style: italic;
    font-size: 19.5px;
    line-height: 25px;
    text-transform: uppercase;
  }
  .service__text {
    color: var(--body-text);
    font-weight: 300;
    font-size: 10px;
    line-height: 12.3px;
    margin: 22px auto 0;
    width: 150px;
    text-transform: none;
    font-style: normal;
  }

  .contact {
    position: absolute;
    right: 48px;
    top: 1018px;
    text-align: right;
    color: var(--white);
  }
  .contact__label { font-size: 36px; font-weight: 400; line-height: 44px; }
  .contact__phone { font-size: 47px; font-weight: 700; line-height: 54px; letter-spacing: 0.5px; }
  .contact__email { font-size: 28.5px; font-weight: 300; line-height: 40px; margin-top: 14px; }
</style>
</head>
<body>
<main class="flyer">
  <svg class="backdrop" viewBox="0 0 848 1200" xmlns="http://www.w3.org/2000/svg">
    <defs>
      <linearGradient id="site-photo-tone" x1="0" y1="0" x2="0" y2="1">
        <stop offset="0" stop-color="#3f5a2c"/>
        <stop offset="0.2" stop-color="#b9b2a4"/>
        <stop offset="0.38" stop-color="var(--soil-light)"/>
        <stop offset="0.7" stop-color="var(--soil-dark)"/>
        <stop offset="1" stop-color="#b88450"/>
      </linearGradient>
    </defs>
    <path class="band band--top" fill="var(--maroon)"
      d="M0,235 C220,245 420,140 580,75 C680,38 780,30 848,33 L848,1200 L0,1200 Z"/>
    <path class="site-photo" role="img" aria-label="Photo of a mini excavator digging a septic pit beside a mobile home, with a worker in the trench"
      fill="url(#site-photo-tone)"
      d="M0,288 C230,290 420,200 590,125 C690,88 790,78 848,80 L848,900 L0,900 Z"/>
    <path class="band band--left" fill="var(--maroon)" d="M0,860 L30,860 L30,900 L0,900 Z"/>
    <path class="wave wave--blue" fill="var(--blue)"
      d="M0,880 C300,872 600,722 848,638 L848,1200 L0,1200 Z"/>
    <path class="wave wave--maroon" fill="var(--maroon)"
      d="M0,1158 C320,1150 600,968 848,898 L848,1200 L0,1200 Z"/>
  </svg>

  <div class="brand">Halvor Grading<br>and Septic</div>

  <section class="service service--pads">
    <div class="service__photo" role="img" aria-label="Concrete septic tank being lifted by a truck crane over a grassy field"></div>
    <h2 class="service__title">Mobile Home<br>Pads
      <p class="service__text">Lorem Ipsum is simply dummy text of the printing and typesetting industry. Lorem Ipsum has been the industry's standard dummy text ever since the 1500s,</p>
    </h2>
  </section>

  <section class="service service--meter">
    <div class="service__photo" role="img" aria-label="Finished mobile home with graded red soil and septic lids in the yard"></div>
    <h2 class="service__title">Meter Pole<br>Placement and<br>Connection
      <p class="service__text">Lorem Ipsum is simply dummy text of the printing and typesetting industry. Lorem Ipsum has been the industry's standard dummy text ever since the 1500s,</p>
    </h2>
  </section>

  <section class="service service--water">
    <div class="service__photo" role="img" aria-label="Water spraying over freshly graded ground near a utility pole"></div>
    <h2 class="service__title">Waterline<br>Connection
      <p class="service__text">Lorem Ipsum is simply dummy text of the printing and typesetting industry. Lorem Ipsum has been the industry's standard dummy text ever since the 1500s,</p>
    </h2>
  </section>

  <section class="service service--septic">
    <div class="service__photo" role="img" aria-label="Mini excavator beside a newly installed septic tank with green lids"></div>
    <h2 class="service__title">On Site Septic<br>System Installs
      <p class="service__text">Lorem Ipsum is simply dummy text of the printing and typesetting industry. Lorem Ipsum has been the industry's standard dummy text ever since the 1500s,</p>
    </h2>
  </section>

  <footer class="contact">
    <p class="contact__label">Call Us</p>
    <p class="contact__phone">555 214 0487</p>
    <p class="contact__email">info@halvorgrading.com</p>
  </footer>
</main>
</body>
</html>
```